Business Card Design

Business Card for professional consulting firm working with large financial institutions.

Target Market(s)

Executive buyers

Industry/Entity Type

Banking

Contact Information for Business Card

Mild creativity wanted. Not boring, but do elaborate artwork.

Font styles to use
Serif
Sans Serif

Colors

Designer to choose colors to be used in the design.

Requirements
Must have
• Standard business card features - company name, individual name, telephone, website, email, locations.
Nice to have
• Two colors
Should not have
• too many colors, fancy printing, cartoons.

```html
<!DOCTYPE html>
<html lang="en">
<head>
<meta charset="utf-8">
<title>Aldmere Partners – Business Card</title>
<link rel="stylesheet" href="https://fonts.googleapis.com/css2?family=Bitter:wght@700&family=Lora:wght@400&family=Roboto:wght@400&display=swap">
<style>
  :root {
    --backdrop: #d8d8d8;
    --card-light: #f4f4f4;
    --card-dark: #1c1d1f;
    --ink: #141414;
    --ink-soft: #444649;
    --paper-white: #ffffff;
  }
  * { margin: 0; padding: 0; box-sizing: border-box; }
  html, body { width: 1200px; height: 960px; overflow: hidden; }
  body { background: var(--backdrop); position: relative; }

  .card { position: absolute; width: 600px; height: 343px; }
  .card--front { left: 314px; top: 113px; background: var(--card-light); }
  .card--back { left: 311px; top: 472px; background: var(--card-dark); }

  .brand {
    position: absolute; left: 98px; top: 58px;
    font-family: "Lora", serif; font-size: 30px; color: var(--ink);
    letter-spacing: 0.2px;
  }

  .holder { position: absolute; left: 377px; top: 145px; width: 223px; }
  .holder__name {
    font-family: "Bitter", serif; font-weight: 700; font-size: 21px;
    color: var(--ink); letter-spacing: 0.5px; padding-bottom: 8px;
    border-bottom: 2px solid var(--ink);
  }
  .holder__address, .holder__contacts {
    font-family: "Roboto", sans-serif; font-size: 14px; color: var(--ink-soft);
    line-height: 17px; list-style: none;
  }
  .holder__address { margin-top: 16px; }
  .holder__contacts { margin-top: 10px; }
  .holder__contacts li { display: flex; align-items: center; height: 19.5px; }
  .holder__contacts svg { width: 13px; height: 13px; margin-right: 9px; fill: var(--ink); }

  .monogram {
    position: absolute; inset: 0; display: flex; align-items: center; justify-content: center;
    font-family: "Lora", serif; font-size: 96px; color: var(--paper-white);
  }
</style>
</head>
<body>
  <section class="card card--front">
    <div class="brand">Aldmere Partners</div>
    <div class="holder">
      <h1 class="holder__name">JORDAN AVERY</h1>
      <p class="holder__address">214 Larchmont Way<br>Juneau, Alaska 99801</p>
      <ul class="holder__contacts">
        <li><svg viewBox="0 0 16 16" aria-hidden="true"><path d="M3.6 1.2l2.3 2.4-1.4 1.8c.9 2 2.4 3.5 4.3 4.4l1.8-1.4 2.4 2.3-1.2 2.4C6.9 12.8 3.2 9.1 1.2 4.2z"/></svg>907 555 0142</li>
        <li><svg viewBox="0 0 16 16" aria-hidden="true"><path d="M1 3h14v1.2L8 8.6 1 4.2z M1 5.6l7 4.4 7-4.4V13H1z"/></svg>hello@aldmere.com</li>
        <li><svg viewBox="0 0 16 16" aria-hidden="true"><circle cx="8" cy="8" r="7"/><path d="M5 4c1.5.5 2 1.8 1.2 3S4.5 8 4 10M10 3.5c-.5 1.5.5 2.5 2 2.5M9 10c1 .5 1.5 1.6 1 3" stroke="#f4f4f4" stroke-width="1.4" fill="none"/></svg>www.aldmere.com</li>
      </ul>
    </div>
  </section>

  <section class="card card--back">
    <div class="monogram">Aldmere</div>
  </section>
</body>
</html>
```